Heritage Hollow Business Cards

Require a business card design. <br/><br/>Needs to include logo (either round or long version) plus these details:<br/>Maya Torvell<br/>Heritage Hollow<br/>maya@kelvadtrading.com.au<br/>02 6481 7395<br/>PO Box Glenwarra NSW 2791<br/>www.heritagehollow.com.au<br/><br/>I need in an editable format so that I can create for multiple staff members. <br/><br/>

Target Market(s)

We are an online store selling renovation products to home owners are builders. Looking for a classic classy design.

Industry/Entity Type

Home And Garden

Contact Information for Business Card

Maya Torvell
Heritage Hollow
maya@kelvadtrading.com.au
02 6481 7395
PO Box Glenwarra NSW 2791
www.heritagehollow.com.au

Colors

Designer to choose colors to be used in the design.

Requirements
Must have
• Must include Logo.

```html
<!DOCTYPE html>
<html lang="en">
<head>
<meta charset="utf-8">
<title>Heritage Hollow Business Cards</title>
<link href="https://fonts.googleapis.com/css2?family=Open+Sans:wght@400;600&family=Questrial&family=Raleway:wght@400&display=swap" rel="stylesheet">
<style>
  :root {
    --backdrop: #c2c2c2;
    --sage: #86a391;
    --sage-deep: #557262;
    --ink: #121317;
    --brand-ink: #2b2b2b;
    --white: #ffffff;
  }
  * { margin: 0; padding: 0; box-sizing: border-box; }
  html, body {
    width: 927px; height: 1200px; overflow: hidden;
    background: var(--backdrop);
  }
  .canvas { position: relative; width: 927px; height: 1200px; }

  .card {
    position: absolute;
    background: var(--sage);
    overflow: hidden;
    box-shadow: 0 14px 18px -10px rgba(0,0,0,0.35);
  }
  .card-front { left: 143px; top: 171px; width: 644px; height: 371px; }
  .card-back  { left: 142px; top: 620px; width: 645px; height: 374px; }

  .band {
    position: absolute; left: 0; right: 0; bottom: 0;
    background: var(--ink);
  }
  .card-front .band { height: 86px; }
  .card-back .band  { height: 95px; }

  .brand-ring {
    position: absolute;
    border: 1px solid var(--brand-ink);
    border-radius: 50%;
  }
  .card-front .brand-ring { left: 188px; top: 17px; width: 292px; height: 292px; }
  .card-back .brand-ring  { left: 37px; top: 63px; width: 170px; height: 170px; }

  .brand-name {
    position: absolute;
    font-family: "Open Sans", sans-serif;
    font-weight: 600;
    color: var(--brand-ink);
    line-height: 0.95;
  }
  .card-front .brand-name { left: 224px; top: 100px; font-size: 46px; }
  .card-back .brand-name  { left: 60px; top: 120px; font-size: 26px; }

  .contact-rail {
    position: absolute; left: 249px; top: 0; width: 25px; height: 279px;
    background: var(--ink);
  }
  .contact-icon {
    position: absolute; left: 235px; width: 54px;
    background: var(--sage-deep);
    display: flex; align-items: center; justify-content: center;
  }
  .contact-icon svg { width: 28px; height: 28px; fill: var(--white); }
  .contact-text {
    position: absolute; left: 294px;
    font-family: "Open Sans", sans-serif;
    color: var(--ink);
    white-space: nowrap;
    line-height: 1;
  }

  .staff-name {
    position: absolute; left: 29px; top: 290px;
    font-family: "Questrial", sans-serif;
    font-size: 38px; letter-spacing: 2px;
    color: var(--white);
  }
  .staff-role {
    position: absolute; left: 30px; top: 332px;
    font-family: "Raleway", sans-serif;
    font-size: 16px; color: var(--white);
  }
</style>
</head>
<body>
<div class="canvas">

  <section class="card card-front">
    <div class="brand-ring"></div>
    <div class="brand-name">Heritage<br>Hollow</div>
    <div class="band"></div>
  </section>

  <section class="card card-back">
    <div class="brand-ring"></div>
    <div class="brand-name">Heritage<br>Hollow</div>

    <div class="contact-rail"></div>

    <div class="contact-icon" style="top:19px;height:47px;">
      <svg viewBox="0 0 24 24" aria-hidden="true"><path d="M6.6 2.5l3 3.3c.5.6.4 1.4-.1 1.9L8 9.2c1.2 2.6 3.9 5.4 6.8 6.8l1.6-1.5c.5-.5 1.3-.6 1.9-.1l3.3 3c.6.5.6 1.4 0 2l-2 2c-.8.8-2 1-3 .6C10.4 19.8 4.2 13.6 2 7.4c-.4-1 0-2.2.7-3l2-1.9c.6-.6 1.4-.6 1.9 0z"/></svg>
    </div>
    <div class="contact-text" style="top:31px;font-size:22px;">02 6481 7395</div>

    <div class="contact-icon" style="top:92px;height:43px;">
      <svg viewBox="0 0 24 24" aria-hidden="true"><path d="M2 5h20v14H2z M3.5 6.5v.4l8.5 6.2 8.5-6.2v-.4z M3.5 17.5h17V9l-5.2 3.8 5 4.2-.6.6-5.2-4.1L12 15l-2.5-1.5-5.2 4.1-.6-.6 5-4.2L3.5 9z" fill-rule="evenodd"/></svg>
    </div>
    <div class="contact-text" style="top:102px;font-size:21px;">maya@kelvadtrading.com.au</div>

    <div class="contact-icon" style="top:157px;height:46px;">
      <svg viewBox="0 0 24 24" aria-hidden="true"><circle cx="12" cy="12" r="10"/><path d="M7 7c1.5-.5 3 0 3.5 1.2S9.5 10 8.6 10.8 8 13 9 14s.5 3-.5 3.5C6.5 16 5 14 4.8 11.5 5.2 9.5 6 8 7 7zm7-3.2c2 .5 3.5 1.8 4.5 3.5-1 .4-2.2.2-2.8.9-.7.8.2 2 1.3 2.5 1 .5.9 2 .4 3.1-.6 1.4-1.9 2.5-2.8 1.6-.7-.8-.2-2-.8-2.9-.6-.9-2.2-.6-2.5-1.8-.3-1.2 1.2-1.8 1.8-2.8.5-.9-.6-1.5-.3-2.5.2-.6.9-.7 1.7-1.6z" fill="#557262"/></svg>
    </div>
    <div class="contact-text" style="top:169px;font-size:21px;">www.heritagehollow.com.au</div>

    <div class="contact-icon" style="top:223px;height:47px;">
      <svg viewBox="0 0 24 24" aria-hidden="true"><path d="M12 1.5c-4 0-7 3-7 7 0 4.8 7 14 7 14s7-9.2 7-14c0-4-3-7-7-7zm0 4a3 3 0 1 1 0 6 3 3 0 0 1 0-6z" fill-rule="evenodd"/></svg>
    </div>
    <div class="contact-text" style="top:238px;font-size:20px;">PO Box Glenwarra NSW 2791</div>

    <div class="band"></div>
    <div class="staff-name">MAYA TORVELL</div>
    <div class="staff-role">Director</div>
  </section>

</div>
</body>
</html>
```